Emerging automotive detailing business

I am starting a small automotive detailing business in hopes of becoming a well-known detailer to work on high end cars. I would like a card to reflect the high quality and time I put into my work. The name of the company is Bright Crest Detailing. I feel like it represents racecars getting off the line at the drag strip as well as an innuendo of "Up the Ladder". I do minor paint correction such as clay barring, multi-step buffing and polishing, waxing, hand washes, etc. I am always striving to learn more and improve my work. My goal is to have total customer satisfaction. This is a female run business but I do not want it to be very girly. Elegant is okay! I have pictures of my personal wrenfield attached, they do not need to be incorporated but if you can think of a cool way to use 1 or all of them, go for it!

Target Market(s)

Anyone that owns a vehicle. Preferably high end vehicles such as Valtori, Castellverde and Morvani but I will also happily work on any car, truck or suv no matter what brand.

Industry/Entity Type

Automotive

Contact Information for Business Card

Bright Crest Detailing
Mira Tolland
4175 Quenhollow Rd
Ashmere PA 17492
Cell phone- call/text- 717-555-0148
email- brightcrestdetails@maildrop-example.com
Instagram: @brightcrestdetailing
Facebook: facebook.com/brightcrestdetailing

Requirements
Must have
• Business name, my name, address, phone number. Listing that I do minor paint correction such as clay barring, multi-step buffing and polishing, waxing, hand washes, interior cleaning, and more. (This last part was in nice to haves but I have realized that I do really want it, so I moved it to must haves.) I want something that is different and eye-catching to my customers. Some people have done this very well with cards already submitted to me, but a lot have not. I didn't mess with the "look and feel bars" much because because I am pretty open to the overall design as long as it is not your basic run of the mill design.
Nice to have
• Something car related. Maybe an appointment time/date line. I do not have a logo, but if you would like to design one and incorporate it, that would be amazing!
Should not have
• Purple and Pink colors. Boring, basic, normal card.

```html
<!DOCTYPE html>
<html lang="en">
<head>
<meta charset="utf-8">
<title>Bright Crest Detailing – Business Card</title>
<link href="https://fonts.googleapis.com/css2?family=Josefin+Sans:wght@300&family=Quicksand:wght@400;500&display=swap" rel="stylesheet">
<style>
  :root {
    --stage: #efefef;
    --card-black: #000000;
    --silver-light: #f4f4f4;
    --silver-mid: #c9c9c9;
    --silver-dark: #7a7a7a;
    --title-grey: #cfcfcf;
    --text-light: #ffffff;
    --text-muted: #a9a9a9;
    --ink: #111111;
  }
  html, body {
    margin: 0;
    width: 1200px;
    height: 800px;
    overflow: hidden;
    background: var(--stage);
  }
  .stage {
    position: relative;
    width: 1200px;
    height: 800px;
  }
  .card {
    position: absolute;
    top: 260px;
    width: 500px;
    height: 280px;
    overflow: hidden;
    font-family: "Quicksand", sans-serif;
  }

  /* Front */
  .card-front {
    left: 70px;
    background: var(--card-black);
    color: var(--text-light);
  }
  .brand-name {
    position: absolute;
    top: 22px;
    left: 0;
    width: 410px;
    margin: 0;
    text-align: center;
    font-family: "Josefin Sans", sans-serif;
    font-weight: 300;
    font-size: 44px;
    line-height: 56px;
    letter-spacing: 2px;
    color: var(--title-grey);
    text-transform: uppercase;
  }
  .rule {
    position: absolute;
    height: 2px;
    background: var(--text-light);
  }
  .front-rule { left: 18px; top: 162px; width: 336px; }
  .owner-name {
    position: absolute;
    right: 30px;
    top: 148px;
    font-size: 18px;
    letter-spacing: 0.5px;
    color: var(--text-muted);
  }
  .edge-tab {
    position: absolute;
    right: 0;
    top: 135px;
    width: 20px;
    height: 32px;
    background: var(--silver-dark);
  }
  .contact-list {
    position: absolute;
    left: 18px;
    top: 180px;
    margin: 0;
    padding: 0;
    list-style: none;
    font-size: 12.5px;
    line-height: 18px;
  }
  .contact-list li {
    display: flex;
    align-items: center;
    gap: 6px;
  }
  .contact-list svg { width: 13px; height: 13px; flex: none; }
  .social-mark {
    width: 11px;
    height: 11px;
    margin: 0 1px;
    background: var(--silver-mid);
    flex: none;
  }
  .address {
    position: absolute;
    right: 30px;
    top: 198px;
    margin: 0;
    font-style: normal;
    font-size: 13px;
    line-height: 18px;
    text-align: right;
  }
  .front-band {
    position: absolute;
    left: 0;
    bottom: 0;
    width: 100%;
    height: 26px;
    background: linear-gradient(90deg, var(--silver-dark) 0%, var(--silver-mid) 25%, var(--silver-light) 50%, var(--silver-mid) 75%, var(--silver-dark) 100%);
  }

  /* Back */
  .card-back {
    left: 630px;
    background: linear-gradient(90deg, var(--silver-dark) 0%, var(--silver-light) 30%, var(--silver-mid) 55%, var(--silver-light) 72%, var(--silver-dark) 100%);
    color: var(--ink);
  }
  .services {
    position: absolute;
    top: 54px;
    left: 0;
    width: 100%;
    margin: 0;
    text-align: center;
    font-size: 14.5px;
    line-height: 19px;
    letter-spacing: 0.4px;
    text-transform: uppercase;
  }
  .back-rule { left: 64px; top: 138px; width: 370px; height: 1.5px; background: var(--ink); }
  .appointment {
    position: absolute;
    left: 32px;
    top: 176px;
    display: flex;
    align-items: center;
    gap: 5px;
    font-size: 13px;
  }
  .appointment svg { width: 15px; height: 15px; }
  .appt-field {
    position: absolute;
    top: 204px;
    font-size: 13px;
  }
  .appt-time { left: 50px; }
  .appt-date { left: 233px; }
  .back-band {
    position: absolute;
    left: 0;
    bottom: 0;
    width: 100%;
    height: 26px;
    background: var(--card-black);
  }
</style>
</head>
<body>
<main class="stage">

  <section class="card card-front" aria-label="Business card front">
    <h1 class="brand-name">Bright Crest<br>Detailing</h1>
    <div class="rule front-rule"></div>
    <p class="owner-name" style="margin:0">Mira Tolland</p>
    <div class="edge-tab"></div>

    <ul class="contact-list">
      <li>
        <svg viewBox="0 0 13 13" aria-hidden="true"><rect x="3" y="0.8" width="7" height="11.4" rx="1.2" fill="none" stroke="#fff" stroke-width="1"/><line x1="5.5" y1="10.5" x2="7.5" y2="10.5" stroke="#fff" stroke-width="0.8"/></svg>
        (717) 555-0148
      </li>
      <li>
        <svg viewBox="0 0 13 13" aria-hidden="true"><rect x="0.7" y="2.5" width="11.6" height="8" fill="none" stroke="#fff" stroke-width="1"/><polyline points="0.7,2.5 6.5,7 12.3,2.5" fill="none" stroke="#fff" stroke-width="1"/></svg>
        brightcrestdetails@maildrop-example.com
      </li>
      <li><span class="social-mark"></span>@brightcrestdetailing</li>
      <li><span class="social-mark"></span>@brightcrestdetailing</li>
    </ul>

    <address class="address">4175 Quenhollow Rd<br>Ashmere, PA 17492</address>
    <div class="front-band"></div>
  </section>

  <section class="card card-back" aria-label="Business card back">
    <p class="services">Minor paint correction;<br>Claying, multi-step buffing and polishing,<br>waxing, hand washes, interior cleaning and more!</p>
    <div class="rule back-rule"></div>

    <div class="appointment">
      <svg viewBox="0 0 15 15" aria-hidden="true"><rect x="1" y="2.5" width="13" height="11.5" fill="none" stroke="#111" stroke-width="1.2"/><rect x="1" y="2.5" width="13" height="3" fill="#111"/><line x1="4.5" y1="1" x2="4.5" y2="4" stroke="#111" stroke-width="1.2"/><line x1="10.5" y1="1" x2="10.5" y2="4" stroke="#111" stroke-width="1.2"/><polyline points="5.5,8 9.5,8 7,12.5" fill="none" stroke="#111" stroke-width="1.1"/></svg>
      Your next appointment:
    </div>
    <span class="appt-field appt-time">Time:</span>
    <span class="appt-field appt-date">Date:</span>
    <div class="back-band"></div>
  </section>

</main>
</body>
</html>
```